Business card for denture clinic Veltrimora

We need a new business card with our new logo. We are a denture clinic in New Zealand with our target market being 45+ years old. We would need a space on the back to write our patients next appointment on. We would space for only one appointment rather than a list. We will attach a photo showing an example of this. But of course, we would like to see your twist on this. We want it to be bold and easy to read and a good mixture of professional but modern. We have attached our logo to be used on the card.

Target Market(s)

People aged 45+ needing dentures

Industry/Entity Type

Dental

Contact Information for Business Card

We want our logo on the front and the space to write an appointment on the back. I've attached an example our our old business card showing this. We need to have the technicians details on the front.

Font styles to use
Sans Serif

Colors
0255a3
919191
fbfbfb

Requirements
Must have
• The following details:
• Liam Dorsett BDT, PGDipCDentTech Calverin
• Dental Prosthetist
• Phone numbers: 0800 47 3125
• 09 572 1394
• Email: liam@veltrimora.co.nz
• www.veltrimora.co.nz
• Address: 14 Marlow Crest Road
• Halbrook West
• Auckland 0793
Nice to have
• We would like our business cards to have more than just two colours as we want them to be more vibrant. We have uploaded an example of a business card we liked that showed this.

```html
<!DOCTYPE html>
<html lang="en">
<head>
<meta charset="utf-8">
<title>Veltrimora business card</title>
<link rel="stylesheet" href="https://fonts.googleapis.com/css2?family=Lato:ital,wght@0,400;0,700;0,900;1,400&display=swap">
<style>
  :root {
    --brand-blue: #0255a3;
    --card-blue: #0361a4;
    --ink: #1b1b1b;
    --muted: #555555;
    --paper: #fbfbfb;
    --stage: #ececec;
    --white: #ffffff;
    --watermark: rgba(255, 255, 255, 0.09);
  }
  * { box-sizing: border-box; margin: 0; padding: 0; }
  html, body { width: 1200px; height: 586px; overflow: hidden; }
  body {
    background: var(--stage);
    font-family: "Lato", Arial, sans-serif;
    color: var(--ink);
    position: relative;
  }
  .card {
    position: absolute;
    top: 129px;
    width: 502px;
    height: 300px;
    overflow: hidden;
  }

  /* Back: appointment */
  .card-back { left: 61px; background: var(--card-blue); color: var(--white); }
  .appointment-title {
    position: absolute; top: 49px; left: 0; width: 100%;
    text-align: center; font-size: 14px; font-weight: 700;
    letter-spacing: 3.6px;
  }
  .appointment-title span {
    border-bottom: 1.5px solid var(--white); padding: 0 2px 2px 4px;
  }
  .field { position: absolute; top: 124px; width: 203px; }
  .field-date { left: 39px; }
  .field-time { left: 266px; }
  .field-label { font-size: 13px; display: block; margin-bottom: 5px; }
  .field-box { height: 33px; background: var(--white); border-radius: 4px; }
  .back-watermark {
    position: absolute; top: 210px; left: 0; width: 100%;
    text-align: center; font-size: 44px; font-weight: 900;
    letter-spacing: 6px; color: var(--watermark);
  }

  /* Front: details */
  .card-front { left: 619px; background: var(--paper); }
  .brand { position: absolute; top: 73px; left: 25px; width: 240px; text-align: center; }
  .brand-mark {
    display: block; width: 34px; height: 34px; margin: 0 auto 1px;
    background: var(--brand-blue); border-radius: 3px;
  }
  .brand-name {
    font-size: 22px; font-weight: 700; letter-spacing: 1px; line-height: 1.2;
    color: var(--brand-blue); text-transform: uppercase;
  }
  .hours { position: absolute; top: 164px; right: 280px; text-align: right; font-size: 12px; }
  .hours-title {
    color: var(--brand-blue); font-weight: 700; font-size: 12px;
    display: inline-block; border-bottom: 1px solid var(--brand-blue);
    margin-bottom: 9px;
  }
  .hours-row { line-height: 21px; }
  .hours-row b { font-weight: 700; }
  .divider {
    position: absolute; left: 260px; top: 63px; width: 2px; height: 176px;
    background: linear-gradient(to bottom, rgba(2,85,163,0), var(--brand-blue) 50%, rgba(2,85,163,0));
  }
  .person { position: absolute; left: 288px; top: 73px; }
  .person-name { font-size: 17px; font-weight: 700; color: var(--brand-blue); }
  .person-credentials { font-size: 11px; font-style: italic; color: var(--muted); margin-top: 4px; }
  .person-role { font-size: 11.5px; font-weight: 700; margin-top: 17px; }
  .contacts { position: absolute; left: 288px; top: 162px; list-style: none; font-size: 12.5px; }
  .contacts li { display: flex; align-items: center; height: 23.5px; }
  .contacts svg { width: 18px; height: 18px; margin-right: 8px; flex: none; }
  .address-band {
    position: absolute; left: 0; bottom: 0; width: 100%; height: 24px;
    background: var(--brand-blue); color: var(--white);
    font-size: 13px; font-weight: 700; text-align: center; line-height: 24px;
  }
</style>
</head>
<body>

<section class="card card-back" aria-label="Appointment card back">
  <h2 class="appointment-title"><span>Your Next Appointment</span></h2>
  <div class="field field-date">
    <span class="field-label">Date:</span>
    <div class="field-box"></div>
  </div>
  <div class="field field-time">
    <span class="field-label">Time:</span>
    <div class="field-box"></div>
  </div>
  <div class="back-watermark" aria-hidden="true">VELTRIMORA</div>
</section>

<section class="card card-front" aria-label="Business card front">
  <div class="brand">
    <span class="brand-mark"></span>
    <div class="brand-name">Veltrimora</div>
  </div>

  <div class="hours">
    <div class="hours-title">Opening Hours</div>
    <div class="hours-row"><b>Mon - Thurs:</b> 9.00am - 5.00pm</div>
    <div class="hours-row"><b>Fri - Sat:</b> 9.00am - 1.00pm</div>
  </div>

  <div class="divider"></div>

  <div class="person">
    <div class="person-name">Liam Dorsett BDT</div>
    <div class="person-credentials">PGDipCDentTech Calverin</div>
    <div class="person-role">Dental Prosthetist</div>
  </div>

  <ul class="contacts">
    <li>
      <svg viewBox="0 0 18 18" aria-hidden="true"><circle cx="9" cy="9" r="9" fill="#0255a3"/><path d="M4.5 7.5c0-1.5 2-2.3 4.5-2.3s4.5.8 4.5 2.3l-1.6.3-.4-1.2c-1.6-.5-3.4-.5-5 0l-.4 1.2zM6.3 8.2h5.4l1.3 4.3H5z" fill="#fff"/></svg>
      0800 47 3125
    </li>
    <li>
      <svg viewBox="0 0 18 18" aria-hidden="true"><circle cx="9" cy="9" r="9" fill="#0255a3"/><path d="M4.5 7.5c0-1.5 2-2.3 4.5-2.3s4.5.8 4.5 2.3l-1.6.3-.4-1.2c-1.6-.5-3.4-.5-5 0l-.4 1.2zM6.3 8.2h5.4l1.3 4.3H5z" fill="#fff"/></svg>
      09 572 1394
    </li>
    <li>
      <svg viewBox="0 0 18 18" aria-hidden="true"><circle cx="9" cy="9" r="9" fill="#0255a3"/><rect x="4.5" y="5.8" width="9" height="6.4" fill="#fff"/><path d="M4.5 5.8L9 9.6l4.5-3.8" fill="none" stroke="#0255a3" stroke-width="1"/></svg>
      liam@veltrimora.co.nz
    </li>
    <li>
      <svg viewBox="0 0 18 18" aria-hidden="true"><circle cx="9" cy="9" r="9" fill="#0255a3"/><g fill="none" stroke="#fff" stroke-width="1"><circle cx="9" cy="9" r="4.6"/><ellipse cx="9" cy="9" rx="2" ry="4.6"/><path d="M4.4 9h9.2"/></g></svg>
      www.veltrimora.co.nz
    </li>
  </ul>

  <div class="address-band">14 Marlow Crest Road, Halbrook West Auckland 0793</div>
</section>

</body>
</html>
```